Firm Stationery Design

I need a design for stationery, including: Stationery First Page, Stationery Second Sheet, Envelope, Mailing Label for Flat Envelopes, and Business Cards

```html
<!DOCTYPE html>
<html lang="en">
<head>
<meta charset="utf-8">
<title>Harlow Law LLC – Business Cards</title>
<link href="https://fonts.googleapis.com/css2?family=Montserrat:wght@400;500;800&display=swap" rel="stylesheet">
<style>
  :root {
    --backdrop: #2b2b2b;
    --card-black: #161616;
    --ink-white: #ffffff;
    --accent-orange: #f39c1f;
    --accent-bronze: #c98a2a;
    --silver: #cfcfcf;
    --shadow: rgba(0, 0, 0, 0.55);
  }
  * { margin: 0; padding: 0; box-sizing: border-box; }
  html, body {
    width: 1200px;
    height: 689px;
    overflow: hidden;
    background: var(--backdrop);
    font-family: "Montserrat", sans-serif;
  }
  .canvas {
    position: relative;
    width: 1200px;
    height: 689px;
    background: var(--backdrop);
  }
  .card {
    position: absolute;
    top: 196px;
    width: 520px;
    height: 297px;
    background: var(--card-black);
    box-shadow: 0 18px 40px var(--shadow);
    overflow: hidden;
  }
  .card--front { left: 50px; }
  .card--back { left: 630px; }

  /* Front side */
  .pattern-field {
    position: absolute;
    inset: 0;
    background: linear-gradient(100deg, #0b0b0b 0%, #1c1c1c 38%, #6e6e6e 62%, var(--silver) 82%, #bdbdbd 100%);
  }
  .front-brand {
    position: absolute;
    left: 150px;
    top: 108px;
    width: 220px;
    padding: 16px 0;
    background: var(--card-black);
    text-align: center;
  }
  .wordmark {
    display: flex;
    align-items: center;
    justify-content: center;
    gap: 10px;
  }
  .wordmark__square {
    width: 16px;
    height: 16px;
    background: var(--accent-orange);
  }
  .wordmark__name {
    font-weight: 800;
    font-size: 34px;
    letter-spacing: 1px;
    color: var(--ink-white);
    line-height: 1;
  }
  .wordmark__suffix {
    margin-top: 8px;
    font-weight: 800;
    font-size: 12px;
    letter-spacing: 10px;
    color: var(--accent-bronze);
    padding-left: 10px;
  }

  /* Back side */
  .back-brand {
    position: absolute;
    left: 36px;
    top: 118px;
    width: 200px;
    text-align: center;
  }
  .back-brand .wordmark__name { font-size: 36px; }
  .divider {
    position: absolute;
    left: 258px;
    top: 70px;
    width: 1.5px;
    height: 157px;
    background: var(--accent-orange);
  }
  .contact {
    position: absolute;
    left: 280px;
    top: 68px;
    color: var(--ink-white);
  }
  .contact__name {
    font-weight: 800;
    font-size: 19px;
    color: var(--accent-orange);
    letter-spacing: 0.5px;
    line-height: 1.1;
  }
  .contact__role {
    font-size: 12px;
    margin-top: 3px;
  }
  .contact__address {
    font-size: 12px;
    margin-top: 12px;
    line-height: 1.45;
  }
  .contact__list {
    list-style: none;
    margin-top: 12px;
    font-size: 12px;
    line-height: 1.6;
  }
  .contact__list li {
    display: flex;
    align-items: center;
    gap: 7px;
  }
  .contact__list svg { width: 10px; height: 10px; fill: var(--accent-orange); }
</style>
</head>
<body>
<main class="canvas">
  <section class="card card--front" aria-label="Business card front">
    <div class="pattern-field" role="img" aria-label="Repeating chevron pattern fading from black to silver"></div>
    <div class="front-brand">
      <div class="wordmark">
        <span class="wordmark__square"></span>
        <span class="wordmark__name">HARLOW</span>
      </div>
      <div class="wordmark__suffix">LAW LLC</div>
    </div>
  </section>

  <section class="card card--back" aria-label="Business card back">
    <div class="back-brand">
      <div class="wordmark">
        <span class="wordmark__square"></span>
        <span class="wordmark__name">HARLOW</span>
      </div>
      <div class="wordmark__suffix">LAW LLC</div>
    </div>
    <div class="divider"></div>
    <div class="contact">
      <p class="contact__name">DANIEL REYES</p>
      <p class="contact__role">Managing Director</p>
      <p class="contact__address">Your address, City<br>State, Zip 1234</p>
      <ul class="contact__list">
        <li>
          <svg viewBox="0 0 10 10" aria-hidden="true"><path d="M2 0.5 L4 2.5 L3 3.8 Q4.5 6 6.2 7 L7.5 6 L9.5 8 L8 9.5 Q3.5 9 0.5 2 Z"/></svg>
          123 456 789
        </li>
        <li>
          <svg viewBox="0 0 10 10" aria-hidden="true"><path d="M0 2 H10 V8.5 H0 Z M0 2 L5 5.5 L10 2" stroke="#161616" stroke-width="0.8"/></svg>
          info@yourmail.com
        </li>
        <li>
          <svg viewBox="0 0 10 10" aria-hidden="true"><circle cx="5" cy="5" r="4.6"/></svg>
          www.yourwebsite.com
        </li>
      </ul>
    </div>
  </section>
</main>
</body>
</html>
```